Design concept for BrightKestrel.com Support Page

We are about to launch a new support page for our www.brightkestrel.com service for photographers and visual artists. The service provides media management, cloud storage, promotional and secure distribution to our members.

The support page will include FAQs and video tutorials.

In particular we're looking for a header for this page that suggests the user is in the support area of our service - so perhaps an illustration that suggests support could look nice (perhaps repair man or doctor iconography). Something to give this area of our site a different look and something that looks both cool and friendly.

Currently the page looks distinctly sparse and undesigned (see attached screenshot) - something that could be remedied, we feel, by some subtle design enhancements that we can implement using CSS.

```html
<!DOCTYPE html>
<html lang="en">
<head>
<meta charset="utf-8">
<title>BrightKestrel Support</title>
<link rel="stylesheet" href="https://fonts.googleapis.com/css2?family=Open+Sans:wght@300;400;600&family=Signika:wght@400;600&display=swap">
<style>
:root{
  --ink:#3a3a3a;
  --muted:#555b60;
  --brand-blue:#1fadd3;
  --link-blue:#1a8fb5;
  --row-grey:#636970;
  --band-grey:#ededed;
  --field-grey:#bdbdbd;
  --button-dark:#3d3f42;
  --footer-bg:#000;
  --footer-link:#9a9a9a;
  --footer-dim:#6f6f6f;
  --white:#fff;
}
*{box-sizing:border-box;margin:0;padding:0}
html,body{width:784px;height:1200px;overflow:hidden}
body{position:relative;background:var(--white);font-family:"Open Sans",sans-serif;color:var(--ink)}
.abs{position:absolute}

/* header */
.site-header{left:0;top:0;width:784px;height:54px;background:var(--white);border-bottom:1px solid #d8d8d8}
.brand{left:20px;top:12px;display:flex;align-items:center;gap:8px;font-family:"Signika",sans-serif;font-weight:600;font-size:25px;color:#4a4f55;line-height:30px}
.brand-mark{width:20px;height:20px;border:3px solid #4a4f55;border-radius:4px}
.user-menu{left:650px;top:15px;width:116px;height:24px;border:1px solid #cfcfcf;background:var(--white);display:flex;align-items:center;padding-left:4px;font-size:9.5px;color:#222;white-space:nowrap}
.user-avatar{flex:none;width:18px;height:16px;background:linear-gradient(135deg,#6b6b6b,#b7b2a8);margin-right:7px}
.user-caret{margin-left:6px;font-size:7px;color:#888}

/* hero */
.hero{left:0;top:54px;width:784px;height:276px;background:linear-gradient(100deg,#1a8bb2 0%,#2ab2dd 45%,#3ec4ee 60%,#1e9dcb 100%);overflow:hidden}
.hero-frame{left:207px;top:20px;width:310px;height:245px;border:12px solid rgba(255,255,255,.12);background:rgba(255,255,255,.06)}
.hero-art{left:64px;top:66px;width:152px;height:152px;border-radius:50%;background:radial-gradient(circle at 50% 50%,rgba(240,236,220,.55) 0%,rgba(120,200,210,.4) 55%,rgba(220,190,120,.25) 80%,rgba(255,255,255,0) 100%)}
.hero-kicker{left:256px;top:92px;font-weight:300;font-size:26px;color:var(--white);letter-spacing:.3px}
.hero-title{left:254px;top:120px;font-weight:300;font-size:50px;color:var(--white);letter-spacing:-.5px;white-space:nowrap}

/* tutorials */
.tutorials{left:0;top:330px;width:784px;height:348px;background:var(--band-grey)}
.section-title{width:784px;left:0;text-align:center;font-family:"Signika",sans-serif;font-weight:600;font-size:25px;color:var(--ink)}
.section-intro{width:784px;left:0;text-align:center;font-size:12px;line-height:14px;color:var(--muted)}
.video-card{top:461px;width:166px}
.video-thumb{position:relative;width:166px;height:120px}
.play-icon{position:absolute;left:52px;top:32px}
.video-title{margin-top:10px;font-family:"Signika",sans-serif;font-weight:600;font-size:12px;color:var(--link-blue)}
.video-text{margin-top:5px;font-size:9.3px;line-height:11px;color:var(--muted)}

/* faq */
.faq-search{left:259px;top:792px;width:272px;height:26px;display:flex}
.faq-field{width:203px;height:26px;background:var(--field-grey)}
.faq-button{width:69px;height:26px;background:var(--button-dark);color:var(--white);font-size:11.5px;display:flex;align-items:center;justify-content:center}
.faq-list{left:70px;top:854px;width:648px}
.faq-row{height:31px;margin-bottom:1px;border-radius:3px;background:var(--row-grey);color:var(--white);display:flex;align-items:center;font-size:11.8px}
.faq-row.is-open{background:var(--brand-blue)}
.faq-plus{width:18px;height:18px;border-radius:50%;background:var(--white);margin:0 21px 0 18px;display:flex;align-items:center;justify-content:center;color:var(--brand-blue);font-weight:600;font-size:14px;line-height:1}

/* footer */
.site-footer{left:0;top:1084px;width:784px;height:116px;background:var(--footer-bg)}
.footer-links{left:0;top:1110px;width:784px;text-align:center;font-family:"Signika",sans-serif;font-size:10.5px;color:var(--footer-link)}
.footer-links span.sep{margin:0 6px}
.footer-copy{left:0;top:1142px;width:784px;text-align:center;font-size:10px;font-weight:600;color:var(--white)}
.footer-powered{left:0;top:1157px;width:784px;text-align:center;font-size:10px;color:var(--footer-dim)}
</style>
</head>
<body>

<header class="abs site-header">
  <div class="abs brand"><span class="brand-mark"></span>BrightKestrel</div>
  <div class="abs user-menu"><span class="user-avatar" role="img" aria-label="User avatar photo"></span>Mara Lindqvist<span class="user-caret">▼</span></div>
</header>

<section class="abs hero" role="img" aria-label="Blue-tinted photo of a hand holding a photo print in a park">
  <div class="abs hero-frame"></div>
  <div class="abs hero-art" role="img" aria-label="Illustration of a life ring"></div>
  <div class="abs hero-kicker">BrightKestrel Support</div>
  <div class="abs hero-title">We’re happy to help ...</div>
</section>

<section class="abs tutorials"></section>
<h2 class="abs section-title" style="top:366px">Video Tutorials</h2>
<p class="abs section-intro" style="top:403px">Lorem ipsum dolor sit amet, consectetur adipisicing elit, sed do eiusmod tempor incididunt ut labore et<br>dolore magna aliqua. Ut enim ad minim veniam, quis nostrud exercitation ullamco laboris.</p>

<article class="abs video-card" style="left:53px">
  <div class="video-thumb" role="img" aria-label="Photo of a camera on a strap" style="background:linear-gradient(120deg,#d6c9a0,#f2ead2 45%,#c7b48a)">
    <svg class="play-icon" width="58" height="58" viewBox="0 0 58 58"><circle cx="29" cy="29" r="26" fill="none" stroke="#fff" stroke-opacity=".75" stroke-width="3"/><path d="M22 17 L42 29 L22 41 Z" fill="#fff" fill-opacity=".75"/></svg>
  </div>
  <h3 class="video-title">Lorem ipsum dolor</h3>
  <p class="video-text">Lorem ipsum dolor sit amet,<br>consectetur adipisicing elit, sed.</p>
</article>
<article class="abs video-card" style="left:227px">
  <div class="video-thumb" role="img" aria-label="Photo of hands with colourful powder" style="background:linear-gradient(130deg,#5a3a5a,#8a8a2a 45%,#2aa9c8 80%,#23304a)">
    <svg class="play-icon" width="58" height="58" viewBox="0 0 58 58"><circle cx="29" cy="29" r="26" fill="none" stroke="#fff" stroke-opacity=".75" stroke-width="3"/><path d="M22 17 L42 29 L22 41 Z" fill="#fff" fill-opacity=".75"/></svg>
  </div>
  <h3 class="video-title">Do eiusmod tempor</h3>
  <p class="video-text">Do eiusmod tempor incididunt ut<br>labore et dolore magna aliqua.</p>
</article>
<article class="abs video-card" style="left:402px">
  <div class="video-thumb" role="img" aria-label="Close-up photo of a coffee bean on droplets" style="background:radial-gradient(ellipse at 50% 65%,#4a3328 0 22%,#2b6f8a 40%,#123a56 100%)">
    <svg class="play-icon" width="58" height="58" viewBox="0 0 58 58"><circle cx="29" cy="29" r="26" fill="none" stroke="#fff" stroke-opacity=".75" stroke-width="3"/><path d="M22 17 L42 29 L22 41 Z" fill="#fff" fill-opacity=".75"/></svg>
  </div>
  <h3 class="video-title">Ut enim ad minim</h3>
  <p class="video-text">Ut enim ad minim veniam, quis<br>nostrd exercittion ullam laboris.</p>
</article>
<article class="abs video-card" style="left:576px">
  <div class="video-thumb" role="img" aria-label="Silhouette photo of a photographer at sunset" style="background:linear-gradient(90deg,#e8b860,#f2d79a 40%,#3a4250 65%,#101a2a)">
    <svg class="play-icon" width="58" height="58" viewBox="0 0 58 58"><circle cx="29" cy="29" r="26" fill="none" stroke="#fff" stroke-opacity=".75" stroke-width="3"/><path d="M22 17 L42 29 L22 41 Z" fill="#fff" fill-opacity=".75"/></svg>
  </div>
  <h3 class="video-title">Lorem ipsum dolor</h3>
  <p class="video-text">Lorem ipsum dolor sit amet,<br>consectetur adipisicing elit, sed.</p>
</article>

<h2 class="abs section-title" style="top:713px">Frequently Asked Questions</h2>
<p class="abs section-intro" style="top:751px">Lorem ipsum dolor sit amet, consectetur adipisicing elit, sed do eiusmod tempor incididunt ut labore et<br>dolore magna aliqua. Ut enim ad minim veniam, quis nostrud exercitation ullamco laboris.</p>
<div class="abs faq-search"><div class="faq-field"></div><div class="faq-button">search</div></div>

<div class="abs faq-list">
  <div class="faq-row is-open"><span class="faq-plus">+</span>Uploading Files Using the Drag and Drop Uploader</div>
  <div class="faq-row"><span class="faq-plus">+</span>Publishing Files</div>
  <div class="faq-row"><span class="faq-plus">+</span>Creating Galleries</div>
  <div class="faq-row"><span class="faq-plus">+</span>Creating Portfolios</div>
  <div class="faq-row"><span class="faq-plus">+</span>Re-ordering Files within Galleries of Portfolios</div>
  <div class="faq-row"><span class="faq-plus">+</span>Managing Folder and Files</div>
</div>

<footer class="abs site-footer"></footer>
<nav class="abs footer-links">Home<span class="sep">·</span>Contact Us<span class="sep">·</span>Affiliate Program<span class="sep">·</span>Privacy Policy<span class="sep">·</span>Site Terms and Conditions<span class="sep">·</span>About Us</nav>
<p class="abs footer-copy">© Copyright 2014 Harbourline Images Pte Ltd. All rights reserved.</p>
<p class="abs footer-powered">Powered by BrightKestrel</p>

</body>
</html>
```